Need Web Design for Business Process Outsourcing Company (Quorvane)

Quorvane is a business process outsourcing company. Need a simple site similar to http://www.tallowbrinkhire.com/ but with a more professional and credible look. New to the process; not sure where to start and comparing my options. Please let me know what my options are if I choose to go with you. Logo is attached for your reference. Please use same colorway

Reason: I want the final product to be coded. Please confirm you will be able to code final design.

Industry/Entity Type

Business

Coding

Coded - Design and coding required

```html
<!DOCTYPE html>
<html lang="en">
<head>
<meta charset="utf-8">
<title>Quorvane — BPO Business Outsourcing</title>
<link href="https://fonts.googleapis.com/css2?family=Open+Sans:wght@400;600;700&display=swap" rel="stylesheet">
<style>
:root{
  --blue:#1a8ccc;
  --blue-dark:#0c5f93;
  --ink:#333333;
  --muted:#8a8a8a;
  --light:#f2f2f2;
  --line:#e2e2e2;
  --white:#ffffff;
}
*{box-sizing:border-box;margin:0;padding:0}
html,body{width:1200px;height:2381px;overflow:hidden;background:var(--white)}
body{position:relative;font-family:"Open Sans",Arial,sans-serif;color:var(--ink)}
.abs{position:absolute}
.brand{display:flex;align-items:center;gap:10px}
.brand-mark{width:44px;height:44px;background:var(--blue)}
.brand-name{font-size:36px;font-weight:700;color:var(--ink);letter-spacing:-.5px}
.top-contact{top:42px;display:flex;align-items:center;gap:10px;font-size:15px;color:#555}
.top-contact svg{width:24px;height:24px}
.main-nav{top:108px;left:0;width:1200px;height:38px;background:var(--blue)}
.main-nav a{position:absolute;top:0;height:38px;line-height:38px;font-size:11.5px;color:var(--white);text-decoration:none;text-transform:uppercase}
.main-nav a.active{background:var(--blue-dark);left:132px;width:134px;text-align:center}
.hero{top:146px;left:0;width:1200px;height:446px;background:linear-gradient(90deg,#e9eef2 0%,#dfe7ee 45%,#a9b8cb 70%,#6f82a0 100%)}
.hero-kicker{top:104px;left:132px;font-size:38px;font-weight:600;letter-spacing:.5px;color:var(--ink)}
.hero-title{top:152px;left:130px;font-size:60px;font-weight:700;letter-spacing:1px;color:#3a3a3a}
.btn{background:var(--blue);color:var(--white);text-align:center;text-transform:uppercase;font-weight:600}
.hero .btn{top:240px;left:133px;width:163px;height:49px;line-height:49px;font-size:14px}
.dot{width:14px;height:14px;border-radius:50%;background:#c8c8c8}
.dot.on{background:var(--blue)}
.dot.small{width:10px;height:10px;background:rgba(255,255,255,.6)}
.dot.small.on{background:#fff}
.section-title{left:0;width:1200px;text-align:center;font-size:34px;font-weight:700;color:var(--ink)}
.lead{left:225px;width:750px;text-align:center;font-size:11.5px;line-height:23px;color:var(--muted)}
.feature{width:280px;text-align:center}
.feature svg{width:36px;height:40px;fill:var(--blue)}
.feature h3{margin-top:30px;font-size:20px;font-weight:400;color:var(--blue)}
.feature p{margin-top:20px;font-size:11px;line-height:24px;color:var(--muted)}
.services{top:1103px;left:0;width:749px;height:529px;background:var(--light)}
.services-photo{top:1103px;left:749px;width:451px;height:529px;background:linear-gradient(180deg,#e9f0f6 0%,#d9e2ea 45%,#b9c3cd 100%)}
.services h2{position:absolute;top:100px;left:133px;font-size:33px;font-weight:700}
.service{display:flex;gap:22px;width:290px}
.service svg{width:36px;height:36px;fill:var(--blue);flex:none}
.service h3{font-size:19px;font-weight:400;color:var(--blue);text-transform:uppercase}
.service p{margin-top:10px;font-size:11px;line-height:24px;color:var(--muted);width:200px}
.news-photo{width:206px;height:184px;background:linear-gradient(135deg,#1f2a3a 0%,#5f7fa5 50%,#dbe5ee 100%)}
.news-photo.b{background:linear-gradient(135deg,#8fb6dc 0%,#5b6f86 50%,#26303d 100%)}
.news-text{width:225px}
.news-text h3{font-size:20px;font-weight:400;line-height:24px;color:var(--blue);text-transform:uppercase}
.news-text p{margin-top:10px;font-size:11px;line-height:24px;color:var(--muted)}
.news-text .btn{display:block;margin-top:20px;width:91px;height:35px;line-height:35px;font-size:11px;font-weight:400}
.footer{top:2068px;left:0;width:1200px;height:265px;background:var(--light)}
.copyright{top:2333px;left:0;width:1200px;height:48px;border-top:1px solid var(--line);background:var(--light);text-align:center;line-height:48px;font-size:11px;color:#777}
.social{display:flex;gap:7px}
.social span{width:31px;height:31px;border:1.5px solid #777;border-radius:50%}
.foot-col h4{font-size:14px;font-weight:600;color:var(--ink);text-transform:uppercase}
.foot-col ul{list-style:none;margin-top:22px}
.foot-col li{font-size:11px;line-height:24px;color:var(--muted)}
.contact-list li{display:flex;gap:12px;align-items:flex-start;line-height:28px;color:#555}
.contact-list svg{width:14px;height:14px;margin-top:7px;fill:#555;flex:none}
.subscribe p{margin-top:22px;font-size:11px;line-height:24px;color:var(--muted);text-align:justify;width:237px}
.email-field{margin-top:20px;width:237px;height:33px;border:1px solid #ccc;background:var(--white);font-size:11px;line-height:31px;padding-left:12px;color:#555}
.subscribe .btn{margin-top:18px;width:84px;height:31px;line-height:31px;font-size:11px;font-weight:400}
</style>
</head>
<body>

<header>
  <div class="abs brand" style="top:32px;left:132px">
    <span class="brand-mark"></span><span class="brand-name">Quorvane</span>
  </div>
  <div class="abs top-contact" style="left:748px">
    <svg viewBox="0 0 24 24"><circle cx="12" cy="12" r="11" fill="none" stroke="#1a8ccc" stroke-width="1.5"/><path d="M8.5 7l2 2-1 1.5c.8 1.6 2 2.8 3.6 3.6l1.5-1 2 2-1.2 1.4c-3.8-.6-7-3.8-7.6-7.6z" fill="#1a8ccc"/></svg>
    <span>580 555 0174</span>
  </div>
  <div class="abs top-contact" style="left:890px">
    <svg viewBox="0 0 24 24"><circle cx="12" cy="12" r="11" fill="none" stroke="#1a8ccc" stroke-width="1.5"/><rect x="7" y="8.5" width="10" height="7" fill="none" stroke="#1a8ccc" stroke-width="1.3"/><path d="M7 8.5l5 4 5-4" fill="none" stroke="#1a8ccc" stroke-width="1.3"/></svg>
    <span>info@Yourmailid.com</span>
  </div>
</header>

<nav class="abs main-nav">
  <a class="active">Who We Are</a>
  <a style="left:277px">Our Solutions</a>
  <a style="left:411px">Our Strategy</a>
  <a style="left:535px">Our Experience</a>
  <a style="left:672px">Security</a>
  <a style="left:769px">News</a>
  <a style="left:846px">Contact Us</a>
</nav>

<section class="abs hero" role="img" aria-label="Businessman holding a tablet over a blurred city skyline">
  <div class="abs hero-kicker">BPO BUSINESS</div>
  <div class="abs hero-title">OUTSOURCING</div>
  <div class="abs btn">View Details</div>
  <div class="abs dot on" style="top:322px;left:133px"></div>
  <div class="abs dot" style="top:322px;left:151px"></div>
  <div class="abs dot" style="top:322px;left:169px"></div>
  <div class="abs dot small on" style="top:398px;left:577px"></div>
  <div class="abs dot small" style="top:398px;left:592px"></div>
  <div class="abs dot small" style="top:398px;left:607px"></div>
</section>

<section>
  <h1 class="abs section-title" style="top:652px">WELCOME TO QUORVANE</h1>
  <p class="abs lead" style="top:722px">Lorem ipsum dolor sit amet, consectetur adipiscing elit, sed do eiusmod tempor incididunt ut labore et dolore magna aliqua. Ut enim ad minim veniam, quis nostrud exercitation ullamco laboris nisi ut aliquip ex ea commodo consequat.</p>

  <div class="abs feature" style="top:822px;left:128px">
    <svg viewBox="0 0 24 24"><path d="M12 8a4 4 0 100 8 4 4 0 000-8zm9 5.5v-3l-2.3-.5a7 7 0 00-.8-1.9l1.3-2-2.1-2.1-2 1.3a7 7 0 00-1.9-.8L12.5 2h-3l-.5 2.5a7 7 0 00-1.9.8l-2-1.3-2.1 2.1 1.3 2a7 7 0 00-.8 1.9L1 10.5v3l2.5.5c.2.7.4 1.3.8 1.9l-1.3 2 2.1 2.1 2-1.3c.6.4 1.2.6 1.9.8l.5 2.5h3l.5-2.5c.7-.2 1.3-.4 1.9-.8l2 1.3 2.1-2.1-1.3-2c.4-.6.6-1.2.8-1.9z"/></svg>
    <h3>REINVENTING</h3>
    <p>Lorem ipsum dolor sit amet, consectetur adipiscing elit, sed do eiusmod tempor incididunt ut labore et dolore magna aliqua. Ut enim ad minim</p>
  </div>
  <div class="abs feature" style="top:822px;left:460px">
    <svg viewBox="0 0 24 28"><path d="M4 1h16v26H4zM7 4v2h2V4zm4 0v2h2V4zm4 0v2h2V4zM7 8v2h2V8zm4 0v2h2V8zm4 0v2h2V8zM7 12v2h2v-2zm4 0v2h2v-2zm4 0v2h2v-2zM7 16v2h2v-2zm4 0v2h2v-2zm4 0v2h2v-2zm-5 5v6h4v-6z" fill-rule="evenodd"/></svg>
    <h3>OUR FACILITIES</h3>
    <p>Lorem ipsum dolor sit amet, consectetur adipiscing elit, sed do eiusmod tempor incididunt ut labore et dolore magna aliqua. Ut enim ad minim</p>
  </div>
  <div class="abs feature" style="top:822px;left:792px">
    <svg viewBox="0 0 36 28" style="width:44px"><circle cx="8" cy="8" r="4.5"/><circle cx="28" cy="8" r="4.5"/><circle cx="18" cy="6" r="5.5"/><path d="M0 22c0-5 3-8 8-8s6 2 6 2-3 3-3 8H0zM36 22c0-5-3-8-8-8s-6 2-6 2 3 3 3 8h11zM9 28c0-8 4-12 9-12s9 4 9 12z"/></svg>
    <h3>OUR PEOPLE</h3>
    <p>Lorem ipsum dolor sit amet, consectetur adipiscing elit, sed do eiusmod tempor incididunt ut labore et dolore magna aliqua. Ut enim ad minim</p>
  </div>
</section>

<section class="abs services">
  <h2>OUR SERVICES</h2>
  <div class="abs service" style="top:205px;left:133px">
    <svg viewBox="0 0 24 24"><path d="M13 3a9 9 0 11-8.5 12l2.3-.8A6.6 6.6 0 1013 5.4V8L8.5 4.2 13 .5z"/><path d="M12 8h2v4.5l3 2-1.1 1.7L12 13.6z"/></svg>
    <div><h3>Customer Service</h3><p>Lorem ipsum dolor sit amet, consectetur adipiscing elit, sed do</p></div>
  </div>
  <div class="abs service" style="top:205px;left:452px">
    <svg viewBox="0 0 24 24"><path d="M1 3h4l1 3h17l-3 9H8l-.6 2H20v2H5l1.8-4.5L3.6 5H1z"/><circle cx="8" cy="21.5" r="1.8"/><circle cx="18" cy="21.5" r="1.8"/></svg>
    <div><h3>Ecommerce</h3><p>Lorem ipsum dolor sit amet, consectetur adipiscing elit, sed do</p></div>
  </div>
  <div class="abs service" style="top:333px;left:133px">
    <svg viewBox="0 0 24 24"><circle cx="12" cy="12" r="11"/><path d="M6 6c2 1 3 3 2 5s2 3 3 5-1 4-2 4M15 3c-1 2 0 3 2 4s3 3 5 2M14 14c2 0 3 2 3 4" fill="none" stroke="#f2f2f2" stroke-width="1.6"/></svg>
    <div><h3>IT Solutions</h3><p>Lorem ipsum dolor sit amet, consectetur adipiscing elit, sed do</p></div>
  </div>
  <div class="abs service" style="top:333px;left:452px">
    <svg viewBox="0 0 24 24"><circle cx="12" cy="7" r="5.5"/><path d="M2 24c0-7 4-10 10-10s10 3 10 10z"/></svg>
    <div><h3>Human Resources</h3><p>Lorem ipsum dolor sit amet, consectetur adipiscing elit, sed do</p></div>
  </div>
</section>
<div class="abs services-photo" role="img" aria-label="Business team meeting in a bright open-plan office"></div>

<section>
  <h2 class="abs section-title" style="top:1696px">LATEST NEWS</h2>
  <div class="abs news-photo" style="top:1789px;left:132px" role="img" aria-label="Hand holding a glowing globe"></div>
  <article class="abs news-text" style="top:1786px;left:367px">
    <h3>Lorem Ipsum<br>Dolor</h3>
    <p>Lorem ipsum dolor sit amet, consectetur adipi-scing elit, sed do eiusmod tempor incididunt ut labore et dolore magna aliqua.</p>
    <span class="btn">Read More</span>
  </article>
  <div class="abs news-photo b" style="top:1789px;left:623px" role="img" aria-label="Hand holding a compass"></div>
  <article class="abs news-text" style="top:1786px;left:853px">
    <h3>Lorem Ipsum<br>Dolor</h3>
    <p>Lorem ipsum dolor sit amet, consectetur adipi-scing elit, sed do eiusmod tempor incididunt ut labore et dolore magna aliqua.</p>
    <span class="btn">Read More</span>
  </article>
</section>

<footer class="abs footer">
  <div class="abs brand" style="top:52px;left:132px">
    <span class="brand-mark"></span><span class="brand-name">Quorvane</span>
  </div>
  <div class="abs social" style="top:139px;left:130px"><span></span><span></span><span></span><span></span><span></span></div>

  <div class="abs foot-col" style="top:50px;left:427px">
    <h4>Quick Links</h4>
    <ul><li>Who We Are</li><li>Our Solutions</li><li>Our Strategy</li><li>Our Experience</li><li>Security</li><li>News</li></ul>
  </div>

  <div class="abs foot-col" style="top:50px;left:603px">
    <h4>Contact Us</h4>
    <ul class="contact-list">
      <li><svg viewBox="0 0 16 16"><path d="M1 5c0-2 3-3 7-3s7 1 7 3v1h-4V5H5v1H1zM3 8h10l1 6H2z"/></svg>408-555-0141/</li>
      <li><svg viewBox="0 0 16 16"><path d="M4 1h8v4H4zM1 6h14v6h-3v3H4v-3H1zm4 4v3h6v-3z" fill-rule="evenodd"/></svg>408-555-0162</li>
      <li><svg viewBox="0 0 16 16"><path d="M1 3h14v10H1zm1.5 1.5L8 9l5.5-4.5z" fill-rule="evenodd"/></svg><span style="text-decoration:underline">info@yourmailid.com</span></li>
      <li style="line-height:18px"><svg viewBox="0 0 16 16" style="margin-top:2px"><path d="M8 0a5 5 0 00-5 5c0 4 5 11 5 11s5-7 5-11a5 5 0 00-5-5zm0 7a2 2 0 110-4 2 2 0 010 4z"/></svg><span>#2868 Lorem ipsum dolor sit<br>amet, consectetur</span></li>
    </ul>
  </div>

  <div class="abs foot-col subscribe" style="top:50px;left:827px">
    <h4>Subscribe Newsletter</h4>
    <p>Enter your email address to receive the latest news our blog.</p>
    <div class="email-field">Email Id</div>
    <div class="btn">Subscribe</div>
  </div>
</footer>
<div class="abs copyright">©2016 Quorvane. All rights reserved.</div>

</body>
</html>
```